Wine Label Design

A wine label for 750ml bottles. Same label for different varieties with the variety / region / vintage to be updated as required.
Brand: Beyond the Ridge
Product Use: Front and Back label suitable for a 750 ml bottle (preferably Burgundy bottles)
Design Brief: Beyond the Ridge is a small winery that produces limited amounts of hand crafted wines that are aimed at the mid to top end of the market and requires a label befitting the work that goes into the creation of the wine. In terms of style i don't have any preconceptions and am open to a broad range of design suggestions at the same level of existing premium brands or innovative brands.
Must Have for Front label
Front Label
Beyond the Ridge
2013
Grampians
Shiraz
750ML (should be in smaller text)
Alc. 14% by Vol. (should be in smaller text)
Must Have for Back Label
Beyond the Ridge
2013
Grampians
Shiraz
www.beyondtheridge.com.au (should be in smaller text)
Product of Australia
Alc.14% by Vol. (should be in smaller text)
Contains preservative 220(should be in smaller text)
Below are some guides for dimensions:
The Front Label Size can be between
100 - 120 mm (Width) x 70 - 85 mm (Height)
The back label size can be between
90 mm (Width) x 70 - 85 mm (Height)
Updates
Target Market(s)
Medium to top end of the wine market who require the label to be a reflection of the wine.
Industry/Entity Type
Product
Colors
Designer to choose colors to be used in the design.
Look and feel
Each slider illustrates characteristics of the customer's brand and the style your logo design should communicate.

```html
<!DOCTYPE html>
<html lang="en">
<head>
<meta charset="utf-8">
<title>Beyond the Ridge – Grampians Shiraz 2013</title>
<link rel="stylesheet" href="https://fonts.googleapis.com/css2?family=Amatic+SC:wght@400;700&display=swap">
<style>
  :root {
    --sky: #82cbe8;
    --orange: #e97822;
    --forest: #006a3c;
    --plum: #8b5179;
    --olive: #6a8f31;
    --paper: #ffffff;
    --ink: #111111;
    --muted: #666666;
    --sketch-light: #f4f4f4;
    --sketch-dark: #d6d6d6;
  }
  * { margin: 0; padding: 0; box-sizing: border-box; }
  html, body { width: 1200px; height: 840px; overflow: hidden; background: var(--paper); }
  .label {
    position: relative;
    width: 1200px;
    height: 840px;
    background: var(--paper);
    font-family: "Amatic SC", cursive;
    color: var(--ink);
  }
  .landscape-art {
    position: absolute;
    left: 0; top: 0;
    width: 592px;
    height: 840px;
    background: linear-gradient(180deg,
      var(--sky) 0%,
      var(--sky) 22%,
      var(--orange) 40%,
      var(--forest) 58%,
      var(--plum) 74%,
      var(--olive) 92%,
      var(--olive) 100%);
  }
  .panel {
    position: absolute;
    left: 592px; top: 0;
    width: 608px; height: 840px;
    text-align: center;
  }
  .brand, .region, .variety, .vintage {
    position: absolute;
    left: 0; right: 0;
    line-height: 1;
    white-space: nowrap;
    text-transform: uppercase;
    transform: translateY(-50%);
  }
  .brand {
    top: 142px;
    font-size: 104px;
    font-weight: 400;
    letter-spacing: 2px;
  }
  .vineyard-scene {
    position: absolute;
    left: 94px; top: 234px;
    width: 424px; height: 236px;
    border-radius: 50% 50% 8px 8px / 30% 30% 8px 8px;
    background: radial-gradient(ellipse at 50% 60%, var(--sketch-dark), var(--sketch-light) 75%);
  }
  .region, .variety, .vintage {
    font-weight: 700;
    font-size: 50px;
  }
  .region { top: 548px; }
  .variety { top: 608px; }
  .vintage { top: 734px; }
  .fine-print {
    position: absolute;
    left: 1176px; top: 760px;
    transform: translate(-50%, -50%) rotate(-90deg);
    font-size: 17px;
    color: var(--muted);
    white-space: nowrap;
    word-spacing: 3px;
  }
</style>
</head>
<body>
<main class="label">
  <div class="landscape-art" role="img" aria-label="Stylised rolling hills in bands of sky blue, orange, deep green, plum and olive"></div>

  <section class="panel">
    <h1 class="brand">Beyond the Ridge</h1>
    <div class="vineyard-scene" role="img" aria-label="Pen sketch of a farmhouse among rolling vineyard rows, trees and a fence"></div>
    <p class="region">Grampians</p>
    <p class="variety">Shiraz</p>
    <p class="vintage">2013</p>
  </section>

  <p class="fine-print">750ML &nbsp; Alc. 14% by Vol.</p>
</main>
</body>
</html>
```